Website Design for WestaKolory.pl – Luxury Wedding Car Rental with Chauffeur

We are looking for a talented designer to create a modern, elegant, and fully responsive website for our new brand – WestyKolory.pl. We are a premium car rental platform in Poland, offering luxury and exotic vehicles exclusively for weddings. All cars come with a professional chauffeur, ensuring a high-end, stress-free, and stylish experience.
Website Purpose:
The website should present our offering in a luxurious, clear, and inspiring way. It must build trust, highlight the prestige of our brand, and encourage inquiries. Our target audience includes engaged couples, wedding planners, and clients seeking a truly exceptional vehicle for their special day.
Design Requirements:
Style: modern, elegant, minimalist
Color palette: white, black, gold, optionally silver – refined and luxurious
Typography: clean, modern, high-end
Layout: clear, intuitive, with large car images and well-defined sections
Fully responsive (desktop, tablet, mobile)
Bilingual layout (Polish/English) must be considered
Pages to Design:
Homepage
About Us
Fleet Overview
Individual Car Pages
Services (Weddings, Photo Shoots, Film Rentals)
Why Us / Unique Selling Points
Contact
FAQ
Inspiration:
Luxury automotive brands (e.g. Varnel-Hoske, Corvash, Elbrin Tusko)
High-end wedding websites
Minimalist layouts with large visuals and elegant typography
Additional Notes:
The design should evoke the emotions of a wedding day – elegance, uniqueness, style, and class. Please avoid flashy colors, excessive graphic effects, or overly decorative elements. Subtlety, prestige, and sophistication are key.

```html
<!DOCTYPE html>
<html lang="en">
<head>
<meta charset="utf-8">
<title>WestaKolory.pl – Luxury Wedding Cars</title>
<link href="https://fonts.googleapis.com/css2?family=Cormorant+Garamond:wght@600;700&family=Montserrat:ital,wght@0,400;0,500;0,600;0,700;1,400&display=swap" rel="stylesheet">
<style>
:root{
  --black:#0b0b0b;
  --ink:#111;
  --gold:#c9a95c;
  --gold-light:#e3c77f;
  --gold-dark:#a8864a;
  --card:#e6e6e6;
  --white:#fff;
  --grey:#9a9a9a;
}
*{margin:0;padding:0;box-sizing:border-box}
html,body{width:1200px;height:4239px;overflow:hidden;background:var(--black);font-family:"Montserrat",sans-serif;color:var(--white)}
.page{position:relative;width:1200px;height:4239px}
.abs{position:absolute}
.serif{font-family:"Cormorant Garamond",serif;font-weight:700}
.gold{color:var(--gold)}
.btn{position:absolute;display:flex;align-items:center;justify-content:center;font-size:13px;font-weight:700;letter-spacing:.5px;text-transform:uppercase;border-radius:4px}
.btn-gold{background:linear-gradient(180deg,var(--gold-light),var(--gold-dark));color:var(--white)}
.btn-outline{border:1px solid var(--gold);color:var(--white)}

/* header */
.header{position:absolute;left:0;top:0;width:1200px;height:94px;background:var(--black)}
.brand{position:absolute;left:62px;top:28px;display:flex;align-items:center;gap:10px;font-family:"Cormorant Garamond",serif;font-weight:700;font-size:30px;color:var(--gold)}
.brand i{display:block;width:14px;height:14px;border-radius:50%;background:var(--gold)}
.nav a{position:absolute;top:36px;font-size:14px;color:var(--white);text-decoration:none}
.nav a.active{color:var(--gold)}

/* hero */
.hero{position:absolute;left:0;top:94px;width:1200px;height:589px;background:linear-gradient(180deg,#3a3a36 0%,#55534e 45%,#6b6a66 75%,#4b4a47 100%)}
.hero h1{position:absolute;left:0;width:1200px;top:58px;text-align:center;font-size:48px;letter-spacing:-.5px}
.hero p{position:absolute;left:0;width:1200px;top:118px;text-align:center;font-size:18px}
.lang{position:absolute;left:1124px;top:18px;width:68px;height:26px;border:1px solid var(--gold);border-radius:4px;background:#222;font-size:10px;font-weight:700;display:flex;align-items:center;justify-content:center}
.dots{position:absolute;display:flex;gap:8px}
.dots span{width:13px;height:13px;border-radius:50%;border:1.5px solid #ccc}
.dots span.on{background:var(--gold-light);border-color:var(--gold-light)}

/* promo */
.promo{position:absolute;border-radius:6px;overflow:hidden;text-align:center;color:var(--white)}
.promo h3{font-family:"Cormorant Garamond",serif;font-weight:700;font-size:32px;line-height:1.15;margin-top:28px}
.promo .from{position:absolute;left:0;right:0;bottom:66px;font-family:"Cormorant Garamond",serif;font-weight:700;font-size:22px}
.promo .price{position:absolute;left:0;right:0;bottom:26px;font-family:"Cormorant Garamond",serif;font-weight:700;font-size:32px}

/* featured */
.section-title{position:absolute;left:0;width:1200px;text-align:center;font-size:46px}
.rule{position:absolute;height:2px;background:var(--gold)}
.tab{position:absolute;top:1472px;font-size:19px;font-weight:700}
.product{position:absolute;width:228px;height:323px;border:1.5px solid var(--gold);border-radius:8px;background:var(--card);overflow:hidden;color:var(--ink)}
.product .shot{position:absolute;left:0;top:0;width:100%;height:202px;background:#e8e8e8;border-bottom:1.5px solid var(--gold);border-radius:0 0 8px 8px}
.product .name{position:absolute;top:225px;width:100%;text-align:center;font-family:"Cormorant Garamond",serif;font-weight:700;font-size:18px;color:#222}
.product .qv{position:absolute;top:250px;width:100%;text-align:center;font-size:8px;text-decoration:underline;color:#444}
.product .bar{position:absolute;left:0;bottom:0;width:100%;height:40px;background:linear-gradient(180deg,var(--gold-light),var(--gold));display:flex;align-items:center;padding:0 10px;font-size:13px;font-weight:500}
.product .icons{margin-left:auto;display:flex;gap:6px}
.product .icons span{width:20px;height:20px;border-radius:3px;display:flex;align-items:center;justify-content:center}
.icons .fav{background:#fff}
.icons .bag{background:var(--gold-dark)}

/* about */
.about{position:absolute;left:0;top:2436px;width:1200px;height:617px;background:linear-gradient(90deg,#5e6265 0%,#3b3e40 35%,#1a1a1a 58%,#0e0e0e 100%)}
.about h2{position:absolute;left:650px;top:100px;font-size:46px}
.about p{position:absolute;left:645px;top:195px;width:440px;font-size:16px;line-height:26px}

/* reviews */
.review{position:absolute;top:3297px;width:312px;height:362px;background:var(--white);border-radius:18px 0 18px 0;color:#333}
.review .q{position:absolute;left:26px;top:30px;font-family:"Cormorant Garamond",serif;font-size:80px;line-height:1;color:var(--gold);opacity:.6}
.review p{position:absolute;left:26px;top:58px;width:270px;font-size:12px;font-style:italic;line-height:21px;text-indent:66px}
.review .who{position:absolute;left:26px;top:278px;display:flex;align-items:center;gap:14px}
.review .avatar{width:52px;height:52px;border-radius:50%;border:2px solid var(--gold);background:linear-gradient(135deg,#d7c4a8,#8e7a62)}
.review .name{font-size:15px;font-weight:600;color:#222}
.review .stars{color:#f2b90f;font-size:10px;letter-spacing:1px}

/* footer */
.footer{position:absolute;left:0;top:3824px;width:1200px;height:415px;background:radial-gradient(ellipse at 50% 45%,#2c3438 0%,#161a1c 55%,#0b0b0b 100%)}
.fcol{position:absolute;top:103px}
.fcol h4{font-family:"Cormorant Garamond",serif;font-weight:700;font-size:21px;padding-bottom:8px;position:relative}
.fcol h4:after{content:"";position:absolute;left:0;bottom:-2px;width:66px;height:2px;background:var(--gold)}
.fcol ul{list-style:none;margin-top:16px}
.fcol li{font-size:12px;line-height:23.5px}
.social{position:absolute;top:4060px;width:36px;height:36px;border-radius:50%;border:1.5px solid #ddd}
.footer-line{position:absolute;left:110px;top:341px;width:980px;height:1px;background:#333}
.legal{position:absolute;top:368px;font-size:12px}
</style>
</head>
<body>
<div class="page">

  <header class="header">
    <div class="brand"><i></i>WestaKolory</div>
    <nav class="nav">
      <a class="active" style="left:388px">Home</a>
      <a style="left:459px">About</a>
      <a style="left:530px">Fleet Overview</a>
      <a style="left:655px">Individual Car</a>
      <a style="left:772px">Services</a>
      <a style="left:856px">Why Us</a>
      <a style="left:937px">FAQ's</a>
    </nav>
    <div class="btn btn-gold" style="left:1007px;top:21px;width:140px;height:46px;font-size:14px">Contact Us</div>
  </header>

  <section class="hero" role="img" aria-label="White luxury convertible parked on a paved courtyard with greenery behind">
    <div class="lang">ENG</div>
    <h1 class="serif">LUXURY <span class="gold">WEDDING CARS</span></h1>
    <p>Rent a Limousine or a Premium-class Van with a chauffeur.</p>
    <div class="btn btn-gold" style="left:456px;top:163px;width:153px;height:46px">Explore Cars</div>
    <div class="btn btn-outline" style="left:619px;top:163px;width:151px;height:46px">Watch More</div>
    <div class="dots" style="left:570px;top:554px"><span></span><span></span><span class="on"></span></div>
  </section>

  <div class="promo" style="left:81px;top:787px;width:477px;height:234px;background:linear-gradient(135deg,#6d6f70,#3e4143)" role="img" aria-label="Grey premium sedan close-up">
    <h3>LUXURIOUS PREMIUM CARS</h3><div class="from">From</div><div class="price">$99.99</div>
  </div>
  <div class="promo" style="left:576px;top:787px;width:263px;height:234px;background:linear-gradient(180deg,#3a3b55,#151515)" role="img" aria-label="Black limousine at night">
    <h3>ELEGANCE WITH<br>LIMOUSINE</h3><div class="from">From</div><div class="price">$129.99</div>
  </div>
  <div class="promo" style="left:858px;top:787px;width:261px;height:234px;background:linear-gradient(180deg,#5a5a5a,#1c1c1c)" role="img" aria-label="Black premium van with passenger stepping in">
    <h3>PREMIUM VANS</h3><div class="from">From</div><div class="price">$49.99</div>
  </div>
  <div class="promo" style="left:81px;top:1044px;width:261px;height:233px;background:linear-gradient(135deg,#d6b871,#a88548)" role="img" aria-label="Gold-toned photo of a car with a chauffeur">
    <h3>-50% OFF</h3><div class="from" style="bottom:18px">For every 3rd Day</div>
  </div>
  <div class="promo" style="left:362px;top:1044px;width:757px;height:233px;background:linear-gradient(90deg,#9aa4ae,#c5ccd3 60%,#b3bac1)" role="img" aria-label="Black luxury saloon in a bright studio">
    <h3>LUXURY SPORTS CARS</h3>
    <div class="from" style="bottom:26px;text-decoration:underline">Learn More</div>
  </div>

  <h2 class="section-title serif" style="top:1350px">FEATURED <span class="gold">CARS</span></h2>
  <div class="rule" style="left:583px;top:1419px;width:82px"></div>
  <div class="tab gold" style="left:382px">NEW ARRIVALS</div>
  <div class="tab" style="left:586px">BESTSELLERS</div>
  <div class="tab" style="left:770px">SALE</div>
  <div class="rule" style="left:377px;top:1506px;width:146px"></div>

  <div class="product" style="left:110px;top:1565px"><div class="shot" role="img" aria-label="Yellow SUV"></div><div class="name">VELORA MARSK</div><div class="qv">QUICKVIEW</div><div class="bar">4,500.00ZŁ<div class="icons"><span class="fav">★</span><span class="bag"></span></div></div></div>
  <div class="product" style="left:360px;top:1565px"><div class="shot" role="img" aria-label="White SUV"></div><div class="name">VELORA MARSK</div><div class="qv">QUICKVIEW</div><div class="bar">4,500.00ZŁ<div class="icons"><span class="fav">★</span><span class="bag"></span></div></div></div>
  <div class="product" style="left:612px;top:1565px"><div class="shot" role="img" aria-label="Black coupe"></div><div class="name">VELORA MARSK</div><div class="qv">QUICKVIEW</div><div class="bar">4,500.00ZŁ<div class="icons"><span class="fav">★</span><span class="bag"></span></div></div></div>
  <div class="product" style="left:862px;top:1565px"><div class="shot" role="img" aria-label="White convertible"></div><div class="name">VELORA MARSK</div><div class="qv">QUICKVIEW</div><div class="bar">4,500.00ZŁ<div class="icons"><span class="fav">★</span><span class="bag"></span></div></div></div>
  <div class="product" style="left:110px;top:1921px"><div class="shot" role="img" aria-label="Blue convertible"></div><div class="name">VELORA MARSK</div><div class="qv">QUICKVIEW</div><div class="bar">4,500.00ZŁ<div class="icons"><span class="fav">★</span><span class="bag"></span></div></div></div>
  <div class="product" style="left:360px;top:1921px"><div class="shot" role="img" aria-label="Black SUV"></div><div class="name">VELORA MARSK</div><div class="qv">QUICKVIEW</div><div class="bar">4,500.00ZŁ<div class="icons"><span class="fav">★</span><span class="bag"></span></div></div></div>
  <div class="product" style="left:612px;top:1921px"><div class="shot" role="img" aria-label="Silver SUV"></div><div class="name">VELORA MARSK</div><div class="qv">QUICKVIEW</div><div class="bar">4,500.00ZŁ<div class="icons"><span class="fav">★</span><span class="bag"></span></div></div></div>
  <div class="product" style="left:862px;top:1921px"><div class="shot" role="img" aria-label="Blue hypercar"></div><div class="name">VELORA MARSK</div><div class="qv">QUICKVIEW</div><div class="bar">4,500.00ZŁ<div class="icons"><span class="fav">★</span><span class="bag"></span></div></div></div>

  <div class="btn btn-gold" style="left:505px;top:2280px;width:190px;height:46px">See All Products</div>

  <section class="about" role="img" aria-label="Chrome grille of a classic luxury car decorated with a white wedding ribbon">
    <h2 class="serif">ABOUT <span class="gold">US</span></h2>
    <div class="rule" style="left:650px;top:162px;width:70px"></div>
    <p>Make your big day truly unforgettable with effortless, elegant transfers anywhere in Poland. At WestaKolory, our professional drivers are friendly, punctual, and ready to customize every detail to your wedding vision. From the moment we pick you up to your grand exit, ride in comfort and style—leaving you free to focus on the memories that matter.</p>
    <div class="btn btn-gold" style="left:645px;top:436px;width:190px;height:46px">See All Products</div>
  </section>

  <h2 class="section-title serif" style="top:3170px">CUSTOMER <span class="gold">REVIEWS</span></h2>
  <div class="rule" style="left:540px;top:3238px;width:124px"></div>

  <div class="review" style="left:109px"><div class="q">“</div><p>“We rented the V8 Grand for our wedding in Krakow and honestly it was the best choice ever. The car looked insane, people were stopping to take pics. The driver was on time, dressed sharp, very polite and chill. My wife still talks about that ride like it was a fairytale. Totally worth it if you want that wow effect.”</p><div class="who"><div class="avatar" role="img" aria-label="Customer portrait"></div><div><div class="name">Marek T, Niepołomice</div><div class="stars">★★★★★</div></div></div></div>
  <div class="review" style="left:443px"><div class="q">“</div><p>“We rented the V8 Grand for our wedding in Krakow and honestly it was the best choice ever. The car looked insane, people were stopping to take pics. The driver was on time, dressed sharp, very polite and chill. My wife still talks about that ride like it was a fairytale. Totally worth it if you want that wow effect.”</p><div class="who"><div class="avatar" role="img" aria-label="Customer portrait"></div><div><div class="name">Marek T, Niepołomice</div><div class="stars">★★★★★</div></div></div></div>
  <div class="review" style="left:775px"><div class="q">“</div><p>“We rented the V8 Grand for our wedding in Krakow and honestly it was the best choice ever. The car looked insane, people were stopping to take pics. The driver was on time, dressed sharp, very polite and chill. My wife still talks about that ride like it was a fairytale. Totally worth it if you want that wow effect.”</p><div class="who"><div class="avatar" role="img" aria-label="Customer portrait"></div><div><div class="name">Marek T, Niepołomice</div><div class="stars">★★★★★</div></div></div></div>

  <div class="dots" style="left:570px;top:3705px"><span></span><span></span><span class="on"></span></div>

  <footer class="footer" role="img" aria-label="Dark photo of a luxury car front in shadow">
    <div class="brand" style="left:135px;top:142px"><i></i>WestaKolory</div>
    <div class="fcol" style="left:462px"><h4>Quick links</h4><ul><li>About Us</li><li>Blog</li><li>FAQ</li><li>Privacy Policy</li><li>Terms &amp; Conditions</li></ul></div>
    <div class="fcol" style="left:690px"><h4>Links</h4><ul><li>Login</li><li>Order History</li><li>Affiliates</li><li>Newsletter</li><li>Gift Certificate</li><li>Returns</li></ul></div>
    <div class="fcol" style="left:879px"><h4>Support</h4><ul><li>Contact Us</li><li>Store Locations</li><li>Our Brands</li><li>Site Map</li><li>Delivery Information</li><li>Unlimited Links</li></ul></div>
    <div class="footer-line"></div>
    <div class="legal" style="left:110px">Copyright ©2025. All Rights Reserved</div>
    <div class="legal" style="left:861px">Terms of use</div>
    <div class="legal" style="left:971px">Privacy Policy</div>
    <svg class="abs" style="left:1127px;top:302px" width="20" height="50" viewBox="0 0 20 50"><path d="M10 48V4M3 11l7-7 7 7" stroke="#c9a95c" stroke-width="2" fill="none"/></svg>
    <div class="legal" style="left:1126px;top:372px;font-size:10px;font-weight:700">C44</div>
  </footer>
  <div class="social" style="left:199px"></div>
  <div class="social" style="left:254px;background:var(--gold);border-color:var(--gold)"></div>

</div>
</body>
</html>
```